Business Card Design for Software Development Company

I am looking for a business card design the incorporates my new logo (attached below).

Key information to include:
Name: Martin Quelbrook
Title: CEO
Email: martin@brightwellcivic.example
Phone: 555-218-9403
Website: www.brightwellcivic.example

NOTE: This design should be easy to edit so that we can order cards for different members of our team.

```html
<!DOCTYPE html>
<html lang="en">
<head>
<meta charset="utf-8">
<title>BrightwellLabs Business Card</title>
<link rel="stylesheet" href="https://fonts.googleapis.com/css2?family=Montserrat:wght@400;600;700&display=swap">
<style>
  :root {
    --backdrop: #161616;
    --card: #232323;
    --white: #f4f4f4;
    --teal: #12b3a0;
    --teal-dark: #128a78;
    --crimson: #9e1e26;
    --vermilion: #d64f2b;
    --orange: #e67e22;
    --sand: #f0c99a;
    --apricot: #f2b070;
  }
  * { margin: 0; padding: 0; box-sizing: border-box; }
  html, body { width: 1200px; height: 1059px; overflow: hidden; }
  body {
    position: relative;
    background: var(--backdrop);
    font-family: "Montserrat", sans-serif;
    color: var(--white);
  }
  .card {
    position: absolute;
    background: var(--card);
    overflow: hidden;
    box-shadow: 0 10px 26px rgba(0,0,0,.55);
  }
  .card--front { left: 256px; top: 89px; width: 687px; height: 391px; }
  .card--back  { left: 253px; top: 546px; width: 694px; height: 395px; }

  .brand { position: absolute; display: flex; flex-direction: column; align-items: flex-end; }
  .brand__row { display: flex; align-items: center; }
  .brand__mark { background: var(--orange); flex: none; }
  .brand__name { font-weight: 700; color: var(--white); line-height: 1; letter-spacing: -0.5px; }
  .brand__tagline { font-weight: 700; color: var(--white); text-transform: uppercase; white-space: nowrap; }

  .card--front .brand { left: 52px; top: 176px; }
  .card--front .brand__mark { width: 20px; height: 20px; margin-right: 8px; }
  .card--front .brand__name { font-size: 31px; }
  .card--front .brand__tagline { font-size: 4px; margin-top: 1px; }

  .divider {
    position: absolute; left: 343px; top: 122px;
    width: 1px; height: 145px; background: var(--teal);
  }
  .person { position: absolute; left: 370px; top: 120px; }
  .person__name { font-size: 26px; font-weight: 700; line-height: 1.1; white-space: nowrap; }
  .person__first { color: var(--teal); }
  .person__last { color: var(--orange); }
  .person__title { font-size: 16px; font-weight: 400; margin-top: 0; }

  .contacts { position: absolute; left: 370px; top: 194px; list-style: none; }
  .contacts li {
    display: flex; align-items: center; height: 28px;
    font-size: 16.5px; font-weight: 400; white-space: nowrap;
  }
  .contacts svg { width: 11px; height: 11px; margin-right: 8px; fill: var(--orange); flex: none; }

  .stripe { position: absolute; left: 0; bottom: 0; width: 100%; height: 16px; display: flex; }
  .stripe span { flex: 1; }

  .watermark-area {
    position: absolute; left: 0; top: 0; width: 440px; height: 395px;
    background: linear-gradient(160deg, rgba(18,138,120,.22) 0%, rgba(120,60,40,.18) 45%, rgba(35,35,35,0) 80%);
  }
  .card--back .brand { left: 95px; top: 160px; }
  .card--back .brand__mark { width: 36px; height: 36px; margin-right: 14px; }
  .card--back .brand__name { font-size: 66px; }
  .card--back .brand__tagline { font-size: 8px; margin-top: 2px; letter-spacing: .3px; }
</style>
</head>
<body>
  <section class="card card--front">
    <div class="brand">
      <div class="brand__row">
        <span class="brand__mark"></span>
        <span class="brand__name">BrightwellLabs</span>
      </div>
      <span class="brand__tagline">A Division of Brightwell Civic</span>
    </div>

    <div class="divider"></div>

    <div class="person">
      <h1 class="person__name"><span class="person__first">Martin</span> <span class="person__last">Quelbrook</span></h1>
      <p class="person__title">CEO</p>
    </div>

    <ul class="contacts">
      <li>
        <svg viewBox="0 0 12 12" aria-hidden="true"><path d="M1 4.5C1 2.5 3.5 1.5 6 1.5s5 1 5 3l-2 .5-.5-1.5h-5L3 5 1 4.5zM3 6h6l1.5 4.5h-9L3 6zm3 1a1.3 1.3 0 100 2.6A1.3 1.3 0 006 7z"/></svg>
        <span>555-218-9403</span>
      </li>
      <li>
        <svg viewBox="0 0 12 12" aria-hidden="true"><path d="M1 5l5-4 5 4v6H1V5zm1 1v4h8V6L6 8.7 2 6z"/></svg>
        <span>martin@brightwellcivic.example</span>
      </li>
      <li>
        <svg viewBox="0 0 12 12" aria-hidden="true"><path d="M6 .5a5.5 5.5 0 110 11 5.5 5.5 0 010-11zM3 3.5l1.5 2L4 8l2 2 .5-2.5L8 6 6.5 4.5 7 2.5 5 2 3 3.5z"/></svg>
        <span>www.brightwellcivic.example</span>
      </li>
    </ul>

    <div class="stripe" aria-hidden="true">
      <span style="background:var(--teal)"></span>
      <span style="background:var(--teal-dark)"></span>
      <span style="background:var(--crimson)"></span>
      <span style="background:var(--vermilion)"></span>
      <span style="background:var(--orange)"></span>
      <span style="background:var(--sand)"></span>
      <span style="background:var(--apricot)"></span>
    </div>
  </section>

  <section class="card card--back">
    <div class="watermark-area" role="img" aria-label="Large faint brand mark decoration in muted teal and brown tones"></div>
    <div class="brand">
      <div class="brand__row">
        <span class="brand__mark"></span>
        <span class="brand__name">BrightwellLabs</span>
      </div>
      <span class="brand__tagline">A Division of Brightwell Civic</span>
    </div>
  </section>
</body>
</html>
```